"Cedar Hollow Realty" is the name of my real estate company

This is for a: "for sale" sign, looking for a minimalist design, wire frame outline of a midcentury modern homes roof line or elevation?

My name is: Dean Marlowe (needed)
My Cell # is: 415 208 3947 (needed)
My BRE license # is: 02468135 (needed)
BRE needs to be displayed in this format: BRE 02468135 (needed)
The white outline on the sign riders 'pictured" may work on large sign
Note font on pictured rider sign

This design is for a real estate "for sale" sign or sandwich board sign. Do Not include the words "For Sale" on the sign.

The measurements are 36" inches (91.44 cm) Length, or tall X 24" inches (60.90 cm) Wide.

|
3
---- 24 ----
6
|

Sorry I wasn't more specific earlier. I'd like the elements of the sign to be scaled in size according to their importance, from largest to smallest:

My name: Dean Marlowe
My phone number: 415-208-3947
My company name: Cedar Hollow Realty
My license number: BRE 02468135 (This can be much smaller than the smallest text)
Additionally, please incorporate contemporary to mid-century modern elements on the wire frame roofline or a simple roof-like design.

Thank you!

Best regards,
Dean

```html
<!DOCTYPE html>
<html lang="en">
<head>
<meta charset="utf-8">
<title>Dean Marlowe – Cedar Hollow Realty Sign</title>
<link rel="stylesheet" href="https://fonts.googleapis.com/css2?family=Nunito:wght@400;600&display=swap">
<style>
  :root {
    --backdrop: #e9e9e6;
    --sign-black: #141212;
    --sign-white: #ffffff;
  }
  html, body {
    margin: 0;
    padding: 0;
    width: 1200px;
    height: 1123px;
    overflow: hidden;
    background: var(--backdrop);
  }
  .sign {
    position: absolute;
    left: 239px;
    top: 20px;
    width: 722px;
    height: 1083px;
    box-sizing: border-box;
    background: var(--sign-black);
    border: 18px solid var(--sign-white);
    color: var(--sign-white);
    font-family: "Nunito", sans-serif;
    display: flex;
    flex-direction: column;
    align-items: center;
    justify-content: space-between;
    padding: 56px 22px 30px;
    text-align: center;
  }
  .roofline {
    display: block;
    width: 520px;
    height: 190px;
  }
  .roofline path {
    fill: none;
    stroke: var(--sign-white);
    stroke-width: 4;
    stroke-linejoin: round;
    stroke-linecap: round;
  }
  .agent-name {
    margin: 0;
    font-weight: 600;
    font-size: 118px;
    line-height: 126px;
    letter-spacing: 2px;
    text-transform: uppercase;
    white-space: nowrap;
  }
  .company {
    margin: 0;
    font-weight: 400;
    font-size: 40px;
    line-height: 48px;
    letter-spacing: 6px;
    text-transform: uppercase;
    white-space: nowrap;
  }
  .contact-panel {
    width: 100%;
    box-sizing: border-box;
    border: 1.5px solid var(--sign-white);
    padding: 14px 0 20px;
  }
  .phone {
    display: block;
    font-weight: 600;
    font-size: 84px;
    line-height: 100px;
    letter-spacing: 1px;
    white-space: nowrap;
  }
  .license {
    display: block;
    margin-top: 4px;
    font-weight: 400;
    font-size: 22px;
    line-height: 28px;
    letter-spacing: 1px;
  }
</style>
</head>
<body>
  <section class="sign" aria-label="Real estate yard sign for Dean Marlowe, Cedar Hollow Realty">
    <svg class="roofline" viewBox="0 0 520 190" aria-hidden="true">
      <path d="M10 30 L250 80 L510 10"/>
      <path d="M60 40 L60 180 L470 180 L470 22"/>
      <path d="M250 80 L250 180"/>
      <path d="M110 180 L110 90 L200 90 L200 180"/>
      <path d="M290 110 L420 110 L420 150 L290 150 Z"/>
      <path d="M355 110 L355 150"/>
    </svg>
    <h1 class="agent-name">Dean<br>Marlowe</h1>
    <p class="company">Cedar Hollow Realty</p>
    <div class="contact-panel">
      <span class="phone">415 208 3947</span>
      <span class="license">BRE 02468135</span>
    </div>
  </section>
</body>
</html>
```